New Webpage for High Class Expert Witness Services Company

We are looking for a minimalist design for a webpage that just has our logo and an entry form offer to connect with one of our Liaisons.
The entry form should just ask for Name, Email, Contact Info and Description of Project.

Company Name is: The Marlowe Crest Advisory Services

Number of Pages Required

1 page

```html
<!DOCTYPE html>
<html lang="en">
<head>
<meta charset="utf-8">
<title>The Marlowe Crest Advisory Services</title>
<link rel="stylesheet" href="https://fonts.googleapis.com/css2?family=Lato:wght@400;700&family=Noto+Serif:wght@700&display=swap">
<style>
:root{
  --ink:#111111;
  --footer:#141414;
  --white:#ffffff;
  --text:#2b2b2b;
  --muted:#666666;
  --field-border:#e3e3e3;
  --rule:#3a3a3a;
  --serif:"Noto Serif", Georgia, serif;
  --sans:"Lato", Arial, sans-serif;
}
*{box-sizing:border-box;margin:0;padding:0}
html,body{width:776px;height:1200px;overflow:hidden;background:var(--white);font-family:var(--sans);color:var(--text)}
.page{position:relative;width:776px;height:1200px}
.topbar{position:absolute;left:0;top:0;width:776px;height:55px;background:var(--ink);display:flex;align-items:center;justify-content:center}
.brand{display:flex;align-items:center;gap:7px;color:var(--white);font-family:var(--sans);font-weight:700;letter-spacing:.5px}
.brand-mark{width:10px;height:10px;background:var(--white)}
.topbar .brand{font-size:14px}
.hero{position:absolute;left:0;top:55px;width:776px;height:388px;
  background:linear-gradient(90deg,rgba(150,150,160,.9) 0%,rgba(60,62,75,.85) 18%,rgba(28,30,44,.9) 50%,rgba(40,42,70,.9) 85%,rgba(70,70,140,.9) 100%),
  linear-gradient(180deg,#2a2c3a 0%,#3b3a44 70%,#6d6a70 100%)}
.hero-text{position:absolute;left:0;top:68px;width:776px;text-align:center;color:var(--white)}
.hero h1{font-family:var(--serif);font-weight:700;font-size:36px;line-height:47px;letter-spacing:.3px;text-shadow:0 2px 6px rgba(0,0,0,.5)}
.hero p{margin-top:9px;font-size:13.5px;font-weight:700;text-shadow:0 1px 4px rgba(0,0,0,.7)}
.consult{position:absolute;left:72px;top:352px;width:633px;height:230px;background:var(--white);border-radius:9px;box-shadow:0 2px 10px rgba(0,0,0,.1)}
.consult h2{font-family:var(--serif);font-weight:700;font-size:24px;text-align:center;margin-top:22px;color:var(--ink)}
.fields{position:absolute;left:26px;top:76px;width:581px;display:grid;grid-template-columns:277px 277px;column-gap:27px;row-gap:11px}
.field{height:31px;border:1px solid var(--field-border);border-radius:5px;box-shadow:0 1px 4px rgba(0,0,0,.08);display:flex;align-items:center;padding:0 13px;font-size:10px;color:var(--muted);gap:9px}
.field svg{flex:none}
.field .chev{margin-left:auto}
.btn{display:inline-flex;align-items:center;justify-content:center;background:var(--ink);color:var(--white);font-weight:700;border-radius:3px}
.submit{position:absolute;left:271px;top:174px;width:105px;height:31px;font-size:11px}
.about-photo{position:absolute;left:78px;top:652px;width:288px;height:250px;border-radius:4px;
  background:radial-gradient(circle at 50% 50%,#bcd4ea 0%,#5d82a6 30%,#26425f 70%,#17293d 100%)}
.frame{position:absolute;border:1.2px solid var(--ink);border-radius:6px}
.frame-a{left:71px;top:645px;width:175px;height:150px;border-right:none;border-bottom:none}
.frame-b{left:198px;top:757px;width:175px;height:150px;border-left:none;border-top:none}
.about{position:absolute;left:416px;top:640px;width:288px}
.about h2{font-family:var(--serif);font-weight:700;font-size:24px;color:var(--ink)}
.about-copy{margin-top:10px;height:166px;overflow:hidden;font-size:9.6px;line-height:16.6px;text-align:justify}
.about-copy p+p{margin-top:7px}
.read-more{position:absolute;left:417px;top:869px;width:83px;height:30px;font-size:11px}
.footer{position:absolute;left:0;top:971px;width:776px;height:229px;background:var(--footer);color:var(--white);text-align:center}
.footer .brand{justify-content:center;font-size:17px;margin-top:76px}
.footer .brand-mark{width:12px;height:12px}
.footer-tag{margin-top:26px;font-size:10px}
.contacts{margin-top:21px;display:flex;justify-content:center;gap:44px;font-size:10px}
.contacts span{display:flex;align-items:center;gap:10px}
.rule{position:absolute;left:72px;top:194px;width:632px;height:1px;background:var(--rule)}
.copyright{position:absolute;left:0;top:204px;width:776px;font-size:10px}
</style>
</head>
<body>
<div class="page">
  <header class="topbar">
    <div class="brand"><span class="brand-mark"></span>Marlowe Crest Advisory Services</div>
  </header>

  <section class="hero" role="img" aria-label="Night-time high-rise office with a desk and chair before tall windows overlooking city towers">
    <div class="hero-text">
      <h1>DEFENSE EXPERTISE<br>WHEN IT MATTERS MOST</h1>
      <p>Connect with seasoned professionals for complex legal matters.</p>
    </div>
  </section>

  <form class="consult">
    <h2>Request a Confidential Consultation</h2>
    <div class="fields">
      <div class="field">
        <svg width="11" height="11" viewBox="0 0 12 12"><circle cx="6" cy="3.2" r="2.7" fill="#777"/><path d="M1 12c0-3 2.2-5 5-5s5 2 5 5z" fill="#777"/></svg>Name
      </div>
      <div class="field">
        <svg width="11" height="11" viewBox="0 0 12 12"><rect x="1" y="1" width="10" height="10" fill="none" stroke="#777" stroke-width="1.3"/><path d="M3 4h6M3 6.5h6M3 9h4" stroke="#777" stroke-width="1.2"/></svg>Description of Project
        <svg class="chev" width="9" height="6" viewBox="0 0 9 6"><path d="M1 1l3.5 3.5L8 1" fill="none" stroke="#333" stroke-width="1.2"/></svg>
      </div>
      <div class="field">
        <svg width="12" height="9" viewBox="0 0 12 9"><rect x=".5" y=".5" width="11" height="8" fill="none" stroke="#777"/><path d="M.5.5l5.5 4.5 5.5-4.5M.5 8.5l4-3.5M11.5 8.5l-4-3.5" fill="none" stroke="#777"/></svg>Email
      </div>
      <div class="field">
        <svg width="11" height="11" viewBox="0 0 12 12"><path d="M2.5 1l2 2.5-1.2 1.4c.8 1.6 2 2.8 3.6 3.6L8.3 7.3 11 9.3 9.8 11C5 10.6 1.2 6.8 1 2.1z" fill="#777"/></svg>Phone Number
      </div>
    </div>
    <button type="button" class="btn submit" style="border:none;font-family:var(--sans)">Submit Inquiry</button>
  </form>

  <div class="frame frame-a"></div>
  <div class="frame frame-b"></div>
  <div class="about-photo" role="img" aria-label="Glowing medical shield with a cross surrounded by floating virus particles on a blue background"></div>

  <section class="about">
    <h2>About Us</h2>
    <div class="about-copy">
      <p>The Marlowe Crest Advisory Services is a trusted provider of elite expert witness support and strategic consulting for attorneys, law firms, corporations, and organizations facing complex legal matters. We specialize in connecting clients with highly qualified professionals whose experience, credibility, and industry knowledge help strengthen cases, clarify technical issues, and support successful outcomes.</p>
      <p>Our team understands that every matter requires discretion, urgency, and precision. That is why we offer a streamlined, confidential process designed to connect you quickly with the right expert for your case.</p>
    </div>
  </section>
  <a class="btn read-more">Read More</a>

  <footer class="footer">
    <div class="brand"><span class="brand-mark"></span>Marlowe Crest Advisory Services</div>
    <p class="footer-tag">Trusted expert witness services and strategic defense consulting for complex legal matters.</p>
    <div class="contacts">
      <span><svg width="11" height="11" viewBox="0 0 12 12"><path d="M2.5 1l2 2.5-1.2 1.4c.8 1.6 2 2.8 3.6 3.6L8.3 7.3 11 9.3 9.8 11C5 10.6 1.2 6.8 1 2.1z" fill="#fff"/></svg>+1 555 010 0199</span>
      <span><svg width="12" height="9" viewBox="0 0 12 9"><rect x=".5" y=".5" width="11" height="8" fill="none" stroke="#fff"/><path d="M.5.5l5.5 4.5 5.5-4.5" fill="none" stroke="#fff"/></svg>info@marlowecrestadvisory.com</span>
    </div>
    <div class="rule"></div>
    <p class="copyright">© 2026 The Marlowe Crest Advisory Services. All Rights Reserved.</p>
  </footer>
</div>
</body>
</html>
```